Need a stunning home page for Car rental company

For a client, I need a slick and sumber home page design. It is a small, local car rental company, with a handful of cars available for rent.
Selling points: affordable lease, availability, always clean cars
The design should be:
- flat and modern
- no, or very few animations/sliders
- CTA: booking form for renting a car.
- 3 featured cars with images and facts (see website) with button to read more about the car.
- fullscreen background video can be an option
- main colour: #efba01
The site is under construction here:
http://solvikutleie.hammerlia.no/
Delivery requirements:
I need a layered & well organised PSD file delivered.

```html
<!DOCTYPE html>
<html lang="en">
<head>
<meta charset="utf-8">
<title>Solvikutleie – Car Rental</title>
<link rel="stylesheet" href="https://fonts.googleapis.com/css2?family=Orbitron:wght@500;700&family=Arimo:wght@400;700&display=swap">
<style>
:root{
  --brand:#efba01;
  --navy:#17202e;
  --title-red:#cf4a26;
  --text:#3a3a3a;
  --white:#ffffff;
  --card-line:#dcdcdc;
}
*{margin:0;padding:0;box-sizing:border-box}
html,body{width:1200px;height:2225px;overflow:hidden;background:var(--white)}
body{position:relative;font-family:"Arimo",Arial,sans-serif;color:var(--text)}
.abs{position:absolute}

/* header */
.site-header{left:0;top:0;width:1200px;height:136px;background:var(--navy)}
.logo{font-family:"Orbitron",sans-serif;font-weight:700;font-size:25px;letter-spacing:1px;color:var(--brand);display:flex;align-items:center;gap:10px}
.logo .dot{width:12px;height:12px;background:var(--brand);border-radius:50%}
.header-logo{left:141px;top:44px}
.call{left:754px;top:12px;color:var(--white);font-size:12px;display:flex;align-items:center;gap:8px;height:28px}
.call b{font-size:16px;font-weight:400}
.lang{left:920px;top:12px;width:139px;height:28px;background:var(--white);display:flex;align-items:center;padding-left:6px;font-size:11px;color:#aaa}
.lang .flag{width:32px;height:20px;background:#2c3f82;border:2px solid #c8202f;margin-right:12px}
.lang .caret{position:absolute;right:10px;top:11px;border:5px solid transparent;border-top:6px solid #888}
.main-nav{left:503px;top:72px;display:flex;font-size:13px}
.main-nav a{color:#9aa3b0;text-decoration:none}
.main-nav a.active{color:var(--brand)}

/* hero */
.hero{left:0;top:136px;width:1200px;height:524px;background:linear-gradient(180deg,#8b97a6 0%,#6d747c 35%,#7d3b3a 55%,#5a5d62 78%,#4a4d52 100%)}
.hero-title{left:141px;top:396px;font-family:"Orbitron",sans-serif;font-weight:500;font-size:32px;color:var(--white);letter-spacing:1px}
.hero-text{left:141px;top:446px;width:480px;font-family:"Orbitron",sans-serif;font-weight:500;font-size:13px;line-height:21px;color:var(--white)}
.btn-book{left:141px;top:543px;width:228px;height:48px;background:var(--brand);border-radius:24px;color:var(--white);font-size:15px;display:flex;align-items:center;padding-left:14px}
.slider-arrow{top:589px;width:43px;height:35px;border:1.5px solid var(--white);display:flex;align-items:center;justify-content:center}

/* headings */
.section-heading{left:0;width:1200px;display:flex;justify-content:center;align-items:center;font-family:"Orbitron",sans-serif;font-weight:700;font-size:21px;color:var(--brand);letter-spacing:.5px}
.heading-rule{left:320px;width:560px;height:6px;background:radial-gradient(ellipse at center,rgba(0,0,0,.22) 0%,rgba(0,0,0,0) 70%)}
.intro{left:141px;top:790px;width:918px;font-size:11.5px;line-height:20px;color:#444}

/* cars */
.car-card{top:1004px;width:276px;height:357px;border:1px solid var(--card-line);border-radius:5px;overflow:hidden;text-align:center}
.car-photo{height:171px}
.car-photo.dark{background:linear-gradient(180deg,#050505 0%,#2b2d31 55%,#0d0d0d 100%)}
.car-photo.van{background:linear-gradient(180deg,#8dc1e3 0%,#dfe6ea 50%,#5a8a3a 80%,#3e6a26 100%)}
.car-name{margin-top:15px;font-family:"Orbitron",sans-serif;font-weight:500;font-size:14px;color:var(--title-red)}
.car-price{margin-top:9px;font-size:17px;color:var(--title-red)}
.car-fact{margin-top:10px;font-size:14px;color:#444}
.btn-more{display:inline-flex;align-items:center;gap:12px;margin-top:18px;background:var(--brand);color:var(--white);font-size:12px;font-weight:700;height:32px;padding:0 20px 0 14px;border-radius:3px}

/* video */
.video-band{left:0;top:1421px;width:1200px;height:316px;background:linear-gradient(160deg,#5b6470 0%,#aab0b6 35%,#d9dcde 55%,#3b4352 80%,#1f2f5a 100%)}
.play{left:552px;top:1532px}

/* services */
.service{top:1890px;width:240px;text-align:center}
.service h3{margin-top:14px;font-family:"Orbitron",sans-serif;font-weight:500;font-size:13px;color:var(--title-red)}
.service p{margin-top:12px;font-size:11.5px;line-height:21px;color:#444}

/* footer */
.site-footer{left:0;top:2106px;width:1200px;height:119px;background:var(--navy)}
.footer-logo{left:141px;top:2133px;font-size:17px}
.footer-logo .dot{width:9px;height:9px}
.footer-links{left:141px;top:2167px;font-size:11.5px;color:var(--white)}
.social{top:2141px;width:29px;height:29px}
.copyright{left:774px;top:2185px;font-size:11.5px;color:var(--white)}
</style>
</head>
<body>

<header class="site-header abs"></header>
<div class="logo header-logo abs"><span class="dot"></span>SOLVIKUTLEIE</div>
<div class="call abs">
  <svg width="18" height="18" viewBox="0 0 24 24"><path d="M6.6 10.8a15 15 0 0 0 6.6 6.6l2.2-2.2c.3-.3.7-.4 1-.2 1.1.4 2.3.6 3.6.6.6 0 1 .4 1 1V20c0 .6-.4 1-1 1A17 17 0 0 1 3 4c0-.6.4-1 1-1h3.5c.6 0 1 .4 1 1 0 1.3.2 2.5.6 3.6.1.3 0 .7-.2 1z" fill="#efba01"/></svg>
  <span>call us:</span><b>40123987</b>
</div>
<div class="lang abs"><span class="flag"></span>English<span class="caret"></span></div>
<nav class="main-nav abs">
  <a class="active" href="#" style="margin-right:33px">Home</a>
  <a href="#" style="margin-right:29px">About Us</a>
  <a href="#" style="margin-right:30px">Our Fleet</a>
  <a href="#" style="margin-right:28px">Services</a>
  <a href="#" style="margin-right:29px">Contact</a>
  <a href="#" style="margin-right:22px">Blog</a>
  <a href="#">Page Templates</a>
</nav>

<section class="hero abs" role="img" aria-label="Red sports car on a hillside road above a city"></section>
<h1 class="hero-title abs">SUPER CARS DEALER</h1>
<p class="hero-text abs">IMGSUPER CARS DEALERVALLIS ELEMENTUM LEO. CUM VIVA MUS LOBORTIS CONSEQUAT PURUS. CURABITUR COMMODO. ETIAM SED NULLA</p>
<div class="btn-book abs">CLICK TO BOOK</div>
<div class="slider-arrow abs" style="left:965px"><svg width="14" height="20" viewBox="0 0 14 20"><path d="M11 2 L3 10 L11 18" stroke="#fff" stroke-width="2.5" fill="none"/></svg></div>
<div class="slider-arrow abs" style="left:1014px"><svg width="14" height="20" viewBox="0 0 14 20"><path d="M3 2 L11 10 L3 18" stroke="#fff" stroke-width="2.5" fill="none"/></svg></div>

<h2 class="section-heading abs" style="top:717px">WELCOME SOLVIKBYEN CAR - HAMMERLIA</h2>
<div class="heading-rule abs" style="top:757px"></div>
<p class="intro abs">Sed ut perspiciatis unde omnis iste natus error sit voluptatem accusantium doloremque laudantium, totam rem aperiam, eaque ipsa quae ab illo inventore veritatis et quasi architecto beatae vitae dicta sunt explicabo&nbsp; Nemo enim ipsam voluptatem quia voluptas sit aspernatur aut odit aut fugit, sed quia consequuntur magni dolores eos qui ratione voluptatem sequi nesciunt. Neque porro quisquam est, qui dolorem ipsum quia dolor sit amet</p>

<h2 class="section-heading abs" style="top:913px">OUR RENTALS OFFER FEATURES</h2>
<div class="heading-rule abs" style="top:953px"></div>

<article class="car-card abs" style="left:141px">
  <div class="car-photo dark" role="img" aria-label="Dark grey sedan on black background"></div>
  <h3 class="car-name">VEXA LS '2014</h3>
  <div class="car-price">€310,000</div>
  <div class="car-fact">Location: Solvik / Nordre / Berg</div>
  <div class="car-fact">Engine: 4.2L V8, petrol</div>
  <div class="btn-more"><svg width="16" height="12" viewBox="0 0 16 12"><path d="M1 7 L3 2 H13 L15 7 V11 H1 Z" fill="#fff"/></svg>Read More</div>
</article>
<article class="car-card abs" style="left:461px">
  <div class="car-photo van" role="img" aria-label="White cargo van on a green lawn"></div>
  <h3 class="car-name">VEXA LS '2014</h3>
  <div class="car-price">€310,000</div>
  <div class="car-fact">Location: Solvik / Nordre / Berg</div>
  <div class="car-fact">Engine: 4.2L V8, petrol</div>
  <div class="btn-more"><svg width="16" height="12" viewBox="0 0 16 12"><path d="M1 7 L3 2 H13 L15 7 V11 H1 Z" fill="#fff"/></svg>Read More</div>
</article>
<article class="car-card abs" style="left:782px">
  <div class="car-photo dark" role="img" aria-label="Dark grey sedan on black background"></div>
  <h3 class="car-name">VEXA LS '2014</h3>
  <div class="car-price">€310,000</div>
  <div class="car-fact">Location: Solvik / Nordre / Berg</div>
  <div class="car-fact">Engine: 4.2L V8, petrol</div>
  <div class="btn-more"><svg width="16" height="12" viewBox="0 0 16 12"><path d="M1 7 L3 2 H13 L15 7 V11 H1 Z" fill="#fff"/></svg>Read More</div>
</article>

<section class="video-band abs" role="img" aria-label="White van driving on a road, video still"></section>
<svg class="play abs" width="95" height="95" viewBox="0 0 95 95"><circle cx="47.5" cy="47.5" r="43" stroke="#fff" stroke-opacity=".85" stroke-width="6" fill="none"/><path d="M37 30 L66 47.5 L37 65 Z" fill="#fff" fill-opacity=".9"/></svg>

<h2 class="section-heading abs" style="top:1800px">OUR FEATURED SERVICES</h2>
<div class="heading-rule abs" style="top:1840px"></div>

<div class="service abs" style="left:111px">
  <svg width="60" height="60" viewBox="0 0 60 60"><circle cx="30" cy="30" r="26" stroke="#efba01" stroke-width="5" fill="none"/><path d="M30 14 V34" stroke="#efba01" stroke-width="5"/><circle cx="30" cy="40" r="5" fill="#efba01"/></svg>
  <h3>ENGINE INSTALLMENT</h3>
  <p>Phasellus imperdiet libero sit amet<br>ante. Donec convallis elementum<br>Cum musloborti purus.</p>
</div>
<div class="service abs" style="left:351px">
  <svg width="60" height="60" viewBox="0 0 60 60"><path d="M50 30 A20 20 0 1 1 38 11.5" stroke="#efba01" stroke-width="4" fill="none"/><path d="M34 6 L42 12 L34 17" stroke="#efba01" stroke-width="3" fill="none"/><text x="30" y="38" text-anchor="middle" font-family="Arimo,sans-serif" font-weight="700" font-size="17" fill="#efba01">24</text></svg>
  <h3>PROVEN TECHNOLOGY</h3>
  <p>Phasellus imperdiet libero sit amet<br>ante. Donec convallis elementum<br>Cum musloborti purus.</p>
</div>
<div class="service abs" style="left:604px">
  <svg width="60" height="60" viewBox="0 0 60 60"><circle cx="36" cy="22" r="11" stroke="#efba01" stroke-width="7" stroke-dasharray="5 3" fill="none"/><circle cx="20" cy="42" r="7" stroke="#efba01" stroke-width="5" stroke-dasharray="4 2.5" fill="none"/></svg>
  <h3>RESULTS DRIVEN</h3>
  <p>Phasellus imperdiet libero sit amet<br>ante. Donec convallis elementum<br>Cum musloborti purus.</p>
</div>
<div class="service abs" style="left:845px">
  <svg width="60" height="60" viewBox="0 0 60 60"><circle cx="30" cy="30" r="24" stroke="#efba01" stroke-width="6" fill="none"/><path d="M8 28 C18 22 42 22 52 28 M30 34 V52" stroke="#efba01" stroke-width="6" fill="none"/><circle cx="30" cy="31" r="5" fill="#efba01"/></svg>
  <h3>PERFORMANCE</h3>
  <p>Phasellus imperdiet libero sit amet<br>ante. Donec convallis elementum<br>Cum musloborti purus.</p>
</div>

<footer class="site-footer abs"></footer>
<div class="logo footer-logo abs"><span class="dot"></span>SOLVIKUTLEIE</div>
<div class="footer-links abs">Home I About Us I Our Fleet I Services I Contact I Blog I Page Templates</div>
<div class="social abs" style="left:915px;background:#3b5998"></div>
<div class="social abs" style="left:953px;background:#1da1d9"></div>
<div class="social abs" style="left:991px;background:#8a8f96"></div>
<div class="social abs" style="left:1029px;background:#1c75b0"></div>
<div class="copyright abs">Copyrights@solvikutleie 2014. All rights reserved</div>

</body>
</html>
```